PowerPoint Design for KESTREL Polls

KESTREL Polls stands for 'Kindred Evaluation Scales Tracking Regional Electoral Leanings'. It is a collaborative research effort to format and combine multiple sources of public opinion data from around the world into merged datasets. We need a Microsoft PowerPoint design for our conference/workshop presentations and instructional videos used as part of our research efforts and crowdsourced development. The design should match the website design and logo, which are attached to this contest (these are the files from previous successful design contests).

Slides will contain a lot of data visualizations, tables with statistical output (lots of numbers), and figures. Bullet points will be used frequently on slides and larg blocks of text should be avided. Margins should be narrow to maximize space used and the size of fonts must be large enough (24-32+) to be visible at the back of classrooms and conference rooms.
Updates

I was away at a conference and am now busy with teaching preparation, so I need a few extra days to give adequate feedback.

Target Market(s)

academia, government, non-profits, postgraduates, researchers

Font styles to use
Sans Serif

Colors

Designer to choose colors to be used in the design.

Requirements
Must have
• designs for common slide layouts
Nice to have
• thematic link with website design and logo

```html
<!DOCTYPE html>
<html lang="en">
<head>
<meta charset="utf-8">
<title>KESTREL Polls – Table Slide</title>
<link rel="stylesheet" href="https://fonts.googleapis.com/css2?family=Open+Sans:wght@400;600;700&family=Roboto:wght@400;500;700&display=swap">
<style>
  :root {
    --brand-blue: #1478be;
    --accent-blue: #29a3dd;
    --table-head: #115684;
    --row-a: #1274bd;
    --row-b: #0f68a8;
    --row-line: rgba(255,255,255,0.35);
    --heading-grey: #595959;
    --body-grey: #555555;
    --footer-grey: #9d9d9d;
    --white: #ffffff;
  }
  * { margin: 0; padding: 0; box-sizing: border-box; }
  html, body { width: 1200px; height: 900px; overflow: hidden; background: var(--white); }
  .slide { position: relative; width: 1200px; height: 900px; background: var(--white); overflow: hidden; }

  .header-shapes { position: absolute; top: 0; left: 0; }
  .slide-title {
    position: absolute; left: 18px; top: 11px;
    font-family: "Open Sans", sans-serif; font-weight: 700; font-size: 33px;
    color: var(--white); letter-spacing: 0.5px;
  }
  .brand {
    position: absolute; right: 20px; top: 22px;
    display: flex; align-items: center; gap: 8px;
    font-family: "Open Sans", sans-serif; font-weight: 700; font-size: 17px;
    color: var(--brand-blue);
  }
  .brand-dot { width: 14px; height: 14px; border-radius: 50%; background: var(--accent-blue); }

  .section-heading {
    position: absolute; left: 21px; top: 166px;
    font-family: "Roboto", sans-serif; font-weight: 700; font-size: 31px;
    color: var(--heading-grey); letter-spacing: 0.3px;
  }
  .intro {
    position: absolute; left: 23px; top: 217px; width: 1100px;
    font-family: "Roboto", sans-serif; font-size: 21px; line-height: 33px;
    color: var(--body-grey);
  }

  .data-table {
    position: absolute; left: 15px; top: 319px; width: 1163px;
    border-collapse: collapse; table-layout: fixed;
    font-family: "Roboto", sans-serif; color: var(--white);
  }
  .data-table th, .data-table td { text-align: left; border-right: 1px solid var(--row-line); }
  .data-table th:last-child, .data-table td:last-child { border-right: none; }
  .data-table thead th {
    background: var(--table-head); height: 76px; font-weight: 700; font-size: 18px; padding-left: 17px;
  }
  .data-table thead th.col-no { padding-left: 11px; }
  .data-table tbody td {
    height: 57px; font-size: 17px; padding-left: 13px; border-top: 1px solid var(--row-line);
  }
  .data-table tbody td.col-no { padding-left: 19px; }
  .data-table tbody tr:nth-child(odd) td { background: var(--row-a); }
  .data-table tbody tr:nth-child(even) td { background: var(--row-b); }
  .data-table tbody td:nth-child(n+3) { padding-left: 33px; }

  .footer { position: absolute; left: 0; top: 855px; width: 1200px; height: 45px; background: var(--footer-grey); }
  .footer-tab { position: absolute; right: 0; top: 0; }
  .copyright {
    position: absolute; left: 11px; top: 9px;
    font-family: "Open Sans", sans-serif; font-weight: 600; font-size: 20px; color: var(--white);
  }
  .page-number {
    position: absolute; right: 26px; top: 12px;
    font-family: "Open Sans", sans-serif; font-weight: 600; font-size: 15px; color: var(--white);
  }
</style>
</head>
<body>
<div class="slide">
  <svg class="header-shapes" width="1200" height="80" viewBox="0 0 1200 80" aria-hidden="true">
    <polygon points="0,0 1100,0 1100,63 0,63" fill="var(--brand-blue)"/>
    <polygon points="0,67 1080,67 1092,76 0,76" fill="var(--accent-blue)"/>
  </svg>
  <h1 class="slide-title">PROJECT TITLE HERE</h1>
  <div class="brand"><span class="brand-dot"></span>KESTREL</div>

  <h2 class="section-heading">QUISQUE RISUS MAGNA</h2>
  <p class="intro">Lorem ipsum dolor sit amet, consectetur adipiscing elit. Duis ut tortor vitae lorem venenatis rutrum.<br>Lorem ipsum dolor sit amet, consectetur adipiscing elit. Duis ut</p>

  <table class="data-table">
    <colgroup>
      <col style="width:54px"><col style="width:249px"><col style="width:289px"><col style="width:281px"><col style="width:290px">
    </colgroup>
    <thead>
      <tr><th class="col-no">No</th><th>Customer Name</th><th>Items</th><th>Subject Code</th><th>Subject Code</th></tr>
    </thead>
    <tbody>
      <tr><td class="col-no">1</td><td>Daniel Morrow</td><td>Mauris laoreet commodo</td><td>Mauris laoreet commodo</td><td>Mauris laoreet commodo</td></tr>
      <tr><td class="col-no">2</td><td>Daniel Morrow</td><td>Mauris laoreet commodo</td><td>Mauris laoreet commodo</td><td>Mauris laoreet commodo</td></tr>
      <tr><td class="col-no">3</td><td>Daniel Morrow</td><td>Mauris laoreet commodo</td><td>Mauris laoreet commodo</td><td>Mauris laoreet commodo</td></tr>
      <tr><td class="col-no">4</td><td>Daniel Morrow</td><td>Mauris laoreet commodo</td><td>Mauris laoreet commodo</td><td>Mauris laoreet commodo</td></tr>
      <tr><td class="col-no">5</td><td>Daniel Morrow</td><td>Mauris laoreet commodo</td><td>Mauris laoreet commodo</td><td>Mauris laoreet commodo</td></tr>
      <tr><td class="col-no">6</td><td>Daniel Morrow</td><td>Mauris laoreet commodo</td><td>Mauris laoreet commodo</td><td>Mauris laoreet commodo</td></tr>
      <tr><td class="col-no">7</td><td>Daniel Morrow</td><td>Mauris laoreet commodo</td><td>Mauris laoreet commodo</td><td>Mauris laoreet commodo</td></tr>
    </tbody>
  </table>

  <footer class="footer">
    <svg class="footer-tab" width="112" height="45" viewBox="0 0 112 45" aria-hidden="true">
      <polygon points="6,0 112,0 112,45 20,45 0,14" fill="var(--white)"/>
      <polygon points="10,2 112,2 112,45 23,45 5,16" fill="var(--accent-blue)"/>
    </svg>
    <span class="copyright">Copyright text here</span>
    <span class="page-number">01</span>
  </footer>
</div>
</body>
</html>
```